New Business Card Design for Manufacturing

We are an engineering/manufacturing company that offers Advanced machining/assembly/engineering services, as well as innovative products for the heavy duty engine cooling markets.

We are looking to get a new business card designed that is clean and modern looking, but still fits the wide range of technical/skilled work we do.

- We hope to use this design as the base for other design work in new Presentations, web, and print work.

Industry/Entity Type

Engineering

Contact Information for Business Card

Our preferred color of blue is (RGB) 22/71/159 but can vary slightly from that color. Our content will be our Logo and full company name (Vantrell Forge Works, Inc.), company address, name, job title, phone number with extension, cell number, fax number, website, and email address on the cards.
We'd like the full company name next to the logo, but we are open to other interpretations of that layout.
Preferably, we would like the back side to be clean with just our logo, and the front to contain all of the contact information.

Colors
2f74b4
0355a3
85abd2

Requirements
Must have
• - Logo, company name, needed content - We are open to interpretation beyond that.
• - Standard size business card.
• - Horizontal orientation.
• - Enough space for lengthy names / job titles (for example, a job title could read "Directory of Human Resources" or "V.P. of Governmental Affairs"). We need this to look clean, whether the title be short (CEO) or long (as described above).

```html
<!DOCTYPE html>
<html lang="en">
<head>
<meta charset="utf-8">
<title>Vantrell Forge Works – Business Card</title>
<link rel="stylesheet" href="https://fonts.googleapis.com/css2?family=Open+Sans:wght@400;600;800&display=swap">
<style>
  :root {
    --brand-blue: #0c4fa0;
    --band-blue: #0f55a3;
    --sky-blue: #4bb4e6;
    --pale-blue: #a9d3f2;
    --ink-grey: #7a7a7a;
    --paper: #ffffff;
    --backdrop: #8f9194;
    --white: #ffffff;
  }
  * { box-sizing: border-box; margin: 0; padding: 0; }
  html, body { width: 1200px; height: 1000px; overflow: hidden; }
  body {
    background: var(--backdrop);
    font-family: "Open Sans", Arial, sans-serif;
    position: relative;
  }
  .card {
    position: absolute;
    width: 560px;
    height: 320px;
    background: var(--paper);
    overflow: hidden;
    box-shadow: 0 6px 18px rgba(0,0,0,.25);
  }
  .card--front { left: 150px; top: 110px; }
  .card--back  { left: 490px; top: 560px; }

  .card__shapes { position: absolute; inset: 0; }

  .company-name {
    position: absolute; left: 34px; top: 44px;
    color: var(--sky-blue);
    font-weight: 800; font-size: 17px; line-height: 1;
    text-transform: uppercase;
  }
  .company-name small { font-size: 9px; }

  .wordmark {
    position: absolute;
    display: flex; align-items: center; gap: 8px;
    color: var(--brand-blue);
    font-weight: 800; text-transform: uppercase;
  }
  .wordmark__square { background: var(--brand-blue); }
  .card--front .wordmark { left: 230px; top: 30px; font-size: 28px; }
  .card--front .wordmark__square { width: 18px; height: 18px; }

  .person { position: absolute; left: 240px; top: 92px; text-align: center; width: 260px; color: var(--ink-grey); }
  .person__name { font-size: 22px; letter-spacing: 1.5px; font-weight: 400; }
  .person__title { font-size: 12px; letter-spacing: 1px; margin-top: 2px; text-transform: uppercase; }

  .address {
    position: absolute; left: 250px; top: 160px; width: 240px;
    color: var(--white); font-size: 13px; letter-spacing: 1px;
    display: flex; align-items: center; gap: 10px; justify-content: center;
  }

  .contact { position: absolute; list-style: none; color: var(--white); font-size: 13px; letter-spacing: 1px; }
  .contact li { display: flex; align-items: center; gap: 10px; height: 23px; }
  .contact svg { width: 14px; height: 14px; fill: var(--white); flex: none; }
  .contact--phones { left: 40px; top: 232px; }
  .contact--web { left: 310px; top: 188px; }

  .card--back .wordmark { left: 0; right: 0; top: 110px; justify-content: center; font-size: 46px; }
  .card--back .wordmark__square { width: 28px; height: 28px; }
  .site {
    position: absolute; left: 240px; top: 196px; width: 240px; text-align: center;
    color: var(--white); font-size: 16px;
  }
</style>
</head>
<body>

<section class="card card--front" aria-label="Business card front">
  <svg class="card__shapes" viewBox="0 0 560 320" aria-hidden="true">
    <path d="M150 180 Q150 150 180 150 H520 Q545 150 560 165 V200 H150 Z" fill="var(--pale-blue)"/>
    <rect x="0" y="176" width="560" height="144" fill="var(--band-blue)"/>
    <path d="M0 210 H160 Q185 210 185 230 H0 Z" fill="var(--pale-blue)" opacity=".55"/>
    <path d="M225 178 Q225 150 255 150 H470 Q500 150 500 178 Q500 200 475 200 H250 Q225 200 225 178 Z" fill="var(--sky-blue)"/>
  </svg>

  <h2 class="company-name">Vantrell<br>Forge<br>Works <small>Inc</small></h2>

  <div class="wordmark"><span class="wordmark__square"></span>Vantrell</div>

  <div class="person">
    <p class="person__name">NAME OF CEO</p>
    <p class="person__title">Directory of Human Resources</p>
  </div>

  <p class="address">
    <svg width="10" height="14" viewBox="0 0 10 14" aria-hidden="true"><path d="M5 0a5 5 0 0 0-5 5c0 4 5 9 5 9s5-5 5-9a5 5 0 0 0-5-5zm0 7a2 2 0 1 1 0-4 2 2 0 0 1 0 4z" fill="var(--white)"/></svg>
    YOUR COMPANY ADDRESS
  </p>

  <ul class="contact contact--web">
    <li><svg viewBox="0 0 14 14" aria-hidden="true"><circle cx="7" cy="7" r="6.5"/><path d="M1 7h12M7 1v12" stroke="var(--band-blue)" stroke-width="1"/></svg>WEBSITE</li>
    <li><svg viewBox="0 0 14 14" aria-hidden="true"><rect x="0" y="3" width="14" height="9"/><path d="M0 3l7 5 7-5" stroke="var(--band-blue)" stroke-width="1" fill="none"/></svg>EMAIL ADDRESS</li>
  </ul>

  <ul class="contact contact--phones">
    <li><svg viewBox="0 0 14 14" aria-hidden="true"><rect x="1" y="5" width="12" height="8" rx="2"/><path d="M0 5c2-4 12-4 14 0l-3 1-1-2H4L3 6z"/></svg>PHONE NUMBER</li>
    <li><svg viewBox="0 0 14 14" aria-hidden="true"><path d="M3 1l2 3-1 2c1 2 2 3 4 4l2-1 3 2-1 2C6 13 1 8 1 2z"/></svg>CELL NUMBER</li>
    <li><svg viewBox="0 0 14 14" aria-hidden="true"><rect x="3" y="0" width="8" height="4"/><rect x="0" y="4" width="14" height="6" rx="1"/><rect x="3" y="8" width="8" height="6"/></svg>FAX NUMBER</li>
  </ul>
</section>

<section class="card card--back" aria-label="Business card back">
  <svg class="card__shapes" viewBox="0 0 560 320" aria-hidden="true">
    <rect x="0" y="184" width="560" height="2" fill="var(--sky-blue)"/>
    <path d="M230 184 H490 V222 Q490 240 470 240 H250 Q230 240 230 222 Z" fill="var(--sky-blue)"/>
  </svg>
  <div class="wordmark"><span class="wordmark__square"></span>Vantrell</div>
  <p class="site">www.website.com</p>
</section>

</body>
</html>
```